Financial Services Consultant needs a business card

We need a business card for a new consulting company based in Melbourne called
"Quelbrook Insights". Tagline is Measure, Monitor, Save
We would like to see business card designs that are in line with the minimal style of the website www.quelbrook-insights.example
The font I have used on the website is Proxima Nova and would like the same or similar font used on the business card with a minimal design in line with the website Two sided with "QUELBROOK INSIGHTS" MEASURE, MONITOR, SAVE on one side and name, title and contact details on the otther
Updates

Hi All, thanks for your submissions, much appreciated.

I have recently added some colour to my webiste, it is hex #3a7b74 for those that wish to use it
Thanks

Hi all

thanks very much for your design submissions I am very impressed and they are much appreciated.

Interms of general feedback please find below;

Colour: I am trying to stick to a minimal design and colour scheme for my website which is still under construction, up to 3 colours( www.quelbrook-insights.example) it is currently black and white with a small amount of blue/green but I am open to suggestion/interpretations for a consulting company.

Card: I dont mind if it has rounded edges or straight, I was thinking about using a letterpress card if possible

Detail: the detail on the card will include; Name, Title, Mobile, Personal Email, Business Email,Web,Business Address

Once again thanks for submissions

Industry/Entity Type

Business

```html
<!DOCTYPE html>
<html lang="en">
<head>
<meta charset="utf-8">
<title>Quelbrook Insights — Business Card Front</title>
<link rel="stylesheet" href="https://fonts.googleapis.com/css2?family=Montserrat:wght@400;500&display=swap">
<style>
  :root {
    --teal: #3a7b74;
    --teal-soft: #9fc0bd;
    --rule-1: #e1ebe9;
    --rule-2: #cbdcd9;
    --rule-3: #a9c7c3;
    --ink: #0a0a0a;
    --paper: #ffffff;
  }
  * { margin: 0; padding: 0; box-sizing: border-box; }
  html, body {
    width: 1200px;
    height: 758px;
    overflow: hidden;
    background: var(--paper);
  }
  .card {
    position: relative;
    width: 1200px;
    height: 758px;
    background: var(--paper);
    font-family: "Montserrat", sans-serif;
    color: var(--ink);
  }
  .corner-square {
    position: absolute;
  }
  .corner-square--dark {
    left: 0; top: 0;
    width: 71px; height: 71px;
    background: var(--teal);
  }
  .corner-square--light {
    left: 71px; top: 71px;
    width: 75px; height: 75px;
    background: var(--teal-soft);
  }
  .brand {
    position: absolute;
    left: 0;
    width: 1176px;
    top: 318px;
    text-align: center;
  }
  .brand__name {
    font-weight: 400;
    font-size: 68px;
    letter-spacing: 1px;
    line-height: 1;
  }
  .brand__tagline {
    margin-top: 66px;
    font-weight: 500;
    font-size: 19px;
    letter-spacing: 0.5px;
    line-height: 1;
  }
  .accent-rules {
    position: absolute;
    right: 0;
    bottom: 0;
    width: 1200px;
    height: 60px;
  }
  .accent-rule {
    position: absolute;
    right: 0;
  }
  .accent-rule--top { top: 0; left: 865px; height: 6px; background: var(--rule-1); }
  .accent-rule--mid { top: 15px; left: 784px; height: 6px; background: var(--rule-2); }
  .accent-rule--low { top: 30px; left: 714px; height: 6px; background: var(--rule-3); }
  .accent-rule--base { top: 46px; left: 0; height: 14px; background: var(--teal); }
</style>
</head>
<body>
  <main class="card">
    <div class="corner-square corner-square--dark"></div>
    <div class="corner-square corner-square--light"></div>

    <section class="brand">
      <h1 class="brand__name">QUELBROOK INSIGHTS</h1>
      <p class="brand__tagline">MEASURE , MONITOR , SAVE</p>
    </section>

    <div class="accent-rules">
      <div class="accent-rule accent-rule--top"></div>
      <div class="accent-rule accent-rule--mid"></div>
      <div class="accent-rule accent-rule--low"></div>
      <div class="accent-rule accent-rule--base"></div>
    </div>
  </main>
</body>
</html>
```